Founder / concept developer needs business card // Consultant needs VCARD

I need a business card for me as a founding consultant in Berlin. I advise entrepreneurs, especially in the design of business ideas, business plans or financing applications. More information about this in the annexes. My USP: I design / structure complex ideas and projects convincingly so that my client is successful. I want to communicate professionalism, effectiveness and clarity. Colors like from the range BLACK-GRAY-GREEN. I am 27 years old, I have studied business for 7 years. Attachments: - Business card design (only idea, do not focus on it) - Website screenshot (only idea, do not focus on it)

Target Market(s)

Target group: Founder (20-50 yrs, m / w, needy, in "break-up phase") and CONTRACTOR / "financier" (30-55 yrs, m / w, often public service "routine-oriented"). The foundations are in quite different industries: digital, craft, tourism, retail, services, etc. Almost all German.

Industry/Entity Type

Consultant

Contact Information for Business Card

Lukas Brennwald
M. Sc., International Business Administration
Gründungsberater, Konzeptentwickler
www.kelvoran-mitrel.de
Postfach-Zugang@kelvoran.de
Tel. 0481 294 3172

Colors

Designer to choose colors to be used in the design.

Requirements
Must have
• Professionalism, persuasiveness, clarity
Nice to have
• memorability
Should not have
• Schnörkelei

```html
<!DOCTYPE html>
<html lang="de">
<head>
<meta charset="utf-8">
<title>Visitenkarte – Lukas Brennwald</title>
<link rel="stylesheet" href="https://fonts.googleapis.com/css2?family=Source+Sans+3:wght@400;600;700&display=swap">
<style>
  :root {
    --page-bg: #e6e6e4;
    --card-bg: #231f20;
    --accent: #3aaa35;
    --accent-dark: #1f6b2a;
    --accent-light: #8fd08a;
    --text-light: #ffffff;
    --text-muted: #cfcfcf;
    --card-shadow: rgba(0, 0, 0, 0.28);
  }
  * { margin: 0; padding: 0; box-sizing: border-box; }
  html, body {
    width: 1200px;
    height: 844px;
    overflow: hidden;
    background: var(--page-bg);
    font-family: "Source Sans 3", "Myriad Pro", Arial, sans-serif;
  }
  .stage {
    position: relative;
    width: 1200px;
    height: 844px;
  }
  .card {
    position: absolute;
    top: 272px;
    width: 520px;
    height: 300px;
    background: var(--card-bg);
    box-shadow: 0 10px 28px var(--card-shadow);
    overflow: hidden;
  }
  .card--front { left: 60px; }
  .card--back  { left: 620px; }

  /* Front side */
  .band {
    position: absolute;
    left: 0;
    width: 100%;
    height: 13px;
    background: var(--accent);
  }
  .band--top { top: 14px; }
  .band--bottom { bottom: 14px; }

  .contact {
    position: absolute;
    top: 58px;
    left: 0;
    width: 100%;
    text-align: center;
    color: var(--text-light);
    font-size: 13px;
    line-height: 1.3;
  }
  .contact__name {
    color: var(--accent);
    font-size: 19px;
    font-weight: 700;
    letter-spacing: 0.3px;
    text-transform: uppercase;
    line-height: 1.1;
  }
  .contact__role {
    font-size: 12.5px;
  }
  .contact__degree {
    font-size: 11.5px;
    color: var(--text-muted);
    margin-bottom: 16px;
  }
  .contact__label {
    color: var(--accent);
    font-weight: 600;
  }
  .contact__web {
    color: var(--accent);
    font-weight: 700;
    margin-bottom: 14px;
  }

  /* Back side */
  .emblem {
    position: absolute;
    left: 188px;
    top: 78px;
    width: 144px;
    height: 144px;
    background: linear-gradient(160deg, var(--accent) 0%, var(--accent-dark) 55%, var(--accent-light) 100%);
  }
  .edge-tab {
    position: absolute;
    width: 30px;
    height: 40px;
    background: var(--accent);
  }
  .edge-tab::after {
    content: "";
    position: absolute;
    top: 0;
    width: 4px;
    height: 100%;
    background: var(--text-light);
  }
  .edge-tab--right { right: 0; top: 36px; }
  .edge-tab--right::after { left: 0; }
  .edge-tab--left { left: 0; top: 190px; }
  .edge-tab--left::after { right: 0; }
</style>
</head>
<body>
  <main class="stage">
    <section class="card card--front" aria-label="Vorderseite">
      <div class="band band--top"></div>
      <div class="contact">
        <p class="contact__name">Lukas Brennwald</p>
        <p class="contact__role">Gründungsberater, Konzeptentwickler</p>
        <p class="contact__degree">M. Sc., International Business Administration</p>
        <p><span class="contact__label">P:</span> 0481 294 3172</p>
        <p><span class="contact__label">E:</span> Postfach-Zugang@kelvoran.de</p>
        <p class="contact__web">www.kelvoran-mitrel.de</p>
        <p>Linienstraße 47</p>
        <p>Berlin, 10119</p>
      </div>
      <div class="band band--bottom"></div>
    </section>

    <section class="card card--back" aria-label="Rückseite">
      <div class="edge-tab edge-tab--right"></div>
      <div class="emblem" role="img" aria-label="Grünes Würfel-Motiv aus Quadraten"></div>
      <div class="edge-tab edge-tab--left"></div>
    </section>
  </main>
</body>
</html>
```